Detail Shop Business card design

i need a business card design for my new detailing company called 'Brisk's Polish Works'. i want an all black and white design . simple, direct and to the point. i want the designer to choose a fitting font to match the logothe front should have logo, address, phone and email and the back side should have a slogan and text indicating that we offer services on anything including cars, trucks, motorcycles and RVs. slogan will read "we take pride in your ride"
maybe also very small on the back side the IG icon with Brisks_Polish_Works

phone 208.417.6352
address 3847 E Larkin Ave
Spokane WA 99214
email: BrisksPolish@mailvexo.com

Target Market(s)

all ages , auto enthusiasts

Industry/Entity Type

Automotive

Contact Information for Business Card

the front should have logo, address, phone and email and the back side should have a slogan and text indicating that we offer services on anything including cars, trucks, motorcycles and RVs. slogan will read "we take pride in your ride"

phone 208.417.6352
address 3847 E Larkin Ave
Spokane WA 99214

Colors
000000
ffffff

Requirements
Must have
• bold font and very simple design with good spacing
Nice to have
• anything creative from the designer indicating we service any types of vehicles
Should not have
• any colors ,

```html
<!DOCTYPE html>
<html lang="en">
<head>
<meta charset="utf-8">
<title>Brisk's Polish Works — Business Card</title>
<link rel="stylesheet" href="https://fonts.googleapis.com/css2?family=Roboto+Slab:wght@400;700&display=swap">
<style>
  :root {
    --ink: #000000;
    --card-black: #0b0b0b;
    --paper: #ffffff;
    --stage: #e6e6e6;
    --muted: #333333;
  }
  * { box-sizing: border-box; margin: 0; padding: 0; }
  html, body { width: 1200px; height: 930px; overflow: hidden; }
  body {
    background: var(--stage);
    font-family: "Roboto Slab", Georgia, serif;
    position: relative;
  }
  .card {
    position: absolute;
    left: 220px;
    width: 760px;
    height: 434px;
    border-radius: 22px;
    overflow: hidden;
  }
  /* Back side */
  .card-back { top: 20px; background: var(--card-black); color: var(--paper); }
  .back-mark {
    position: absolute; top: 92px; left: 0; right: 0;
    display: flex; align-items: center; justify-content: center; gap: 18px;
  }
  .mark-circle {
    width: 62px; height: 62px; border-radius: 50%;
    border: 4px solid currentColor;
  }
  .mark-name { font-weight: 700; font-size: 40px; letter-spacing: 1px; text-transform: uppercase; }
  .slogan-row {
    position: absolute; top: 262px; left: 0; right: 0;
    display: flex; align-items: center; justify-content: center; gap: 14px;
    font-size: 19px; letter-spacing: 2px; text-transform: uppercase;
  }
  .slogan-rule { width: 70px; height: 1px; background: var(--paper); }
  .services {
    position: absolute; top: 310px; left: 0; right: 0;
    text-align: center; font-size: 22px; letter-spacing: 1.5px; text-transform: uppercase;
  }
  /* Front side */
  .card-front { top: 476px; background: var(--paper); color: var(--ink); }
  .front-mark {
    position: absolute; top: 40px; right: 46px;
    display: flex; align-items: center; gap: 12px;
  }
  .front-mark .mark-circle { width: 46px; height: 46px; border-width: 3px; }
  .front-mark .mark-name { font-size: 26px; }
  .name-row {
    position: absolute; top: 150px; left: 44px; right: 46px;
    display: flex; align-items: center; gap: 16px;
  }
  .person-name { font-weight: 700; font-size: 34px; letter-spacing: 1px; text-transform: uppercase; white-space: nowrap; }
  .name-rule { flex: 1; height: 1px; background: var(--ink); }
  .role-row {
    position: absolute; top: 200px; left: 44px;
    display: flex; align-items: center; gap: 12px; font-size: 20px;
  }
  .role-rule { width: 110px; height: 1px; background: var(--ink); }
  .address { position: absolute; top: 248px; left: 44px; font-size: 20px; line-height: 1.3; }
  .contacts { position: absolute; top: 318px; left: 44px; list-style: none; font-size: 20px; line-height: 1.35; }
  .contacts li { display: flex; align-items: center; gap: 12px; }
  .contacts svg { width: 16px; height: 16px; flex: none; }
</style>
</head>
<body>
  <section class="card card-back" aria-label="Card back">
    <div class="back-mark">
      <span class="mark-circle"></span>
      <span class="mark-name">Brisk's Polish Works</span>
    </div>
    <div class="slogan-row">
      <span class="slogan-rule"></span>
      <span class="slogan">We take pride in your ride</span>
      <span class="slogan-rule"></span>
    </div>
    <p class="services">Cars - Trucks - Motorcycles and RVs</p>
  </section>

  <section class="card card-front" aria-label="Card front">
    <div class="front-mark">
      <span class="mark-circle"></span>
      <span class="mark-name">Brisk's Polish Works</span>
    </div>
    <div class="name-row">
      <span class="person-name">Dorian Walsh</span>
      <span class="name-rule"></span>
    </div>
    <div class="role-row">
      <span class="role">Director</span>
      <span class="role-rule"></span>
    </div>
    <p class="address">3847 E Larkin Ave<br>Spokane WA 99214</p>
    <ul class="contacts">
      <li>
        <svg viewBox="0 0 16 16" aria-hidden="true"><path d="M4 1.5l2.2 3-1.3 1.4a8 8 0 0 0 5.2 5.2l1.4-1.3 3 2.2-1.2 2.3C7.5 14.5 1.5 8.5 1.7 2.7z" fill="#000"/></svg>
        <span>208.417.6352</span>
      </li>
      <li>
        <svg viewBox="0 0 16 16" aria-hidden="true"><rect x="1.5" y="3.5" width="13" height="9" fill="none" stroke="#000" stroke-width="1.4"/><path d="M1.5 3.5L8 9l6.5-5.5" fill="none" stroke="#000" stroke-width="1.4"/></svg>
        <span>BrisksPolish@mailvexo.com</span>
      </li>
      <li>
        <svg viewBox="0 0 16 16" aria-hidden="true"><circle cx="8" cy="8" r="6.3" fill="none" stroke="#000" stroke-width="1.3"/><ellipse cx="8" cy="8" rx="2.7" ry="6.3" fill="none" stroke="#000" stroke-width="1.1"/><path d="M1.7 8h12.6" stroke="#000" stroke-width="1.1"/></svg>
        <span>www.BrisksPolishWorks.com</span>
      </li>
    </ul>
  </section>
</body>
</html>
```